Stonebrace Business Card Design

The Stonebrace Co is an aggregate (crushing) equipment dealer serving Western Canadian provinces. Stonebrace is a distributor of aggregate equipment for different manufacturers.

We are looking to change and update the existing business card which has been used since the existence of the company. A copy of existing card has been attached for reference. The Stonebrace Co logo we want to remain the same and we want the green color to remain the same.

We are wanting something new with a different look. A refreshing card to show a new modern and updated look. No longer wanting to have the manufacturers on the back of the card but something more like our logo on the back of the card with a statement like "Crushing Solutions"

ideas could be:
- card can be different colors on front and back
- front or reverse of the card could possibly be the green color with the logo in black

Target Market(s)

Owners of Aggregate/Crushing companies

Contact Information for Business Card

see above

Requirements
Must have
• - logo to remain same along with same font within logo
• - green color to remain same
Nice to have
• as noted above under project description
Should not have

```html
<!DOCTYPE html>
<html lang="en">
<head>
<meta charset="utf-8">
<title>The Stonebrace Co – Business Card</title>
<link href="https://fonts.googleapis.com/css2?family=Roboto:wght@400;700&display=swap" rel="stylesheet">
<style>
  :root {
    --brand-green: #8a8c0a;
    --ink: #2a2a2a;
    --paper: #f7f7f5;
    --backdrop: #3a3a3a;
    --white: #ffffff;
  }
  * { box-sizing: border-box; margin: 0; padding: 0; }
  html, body { width: 1200px; height: 911px; overflow: hidden; }
  body {
    background: var(--backdrop);
    font-family: "Roboto", Arial, sans-serif;
    position: relative;
  }
  .card {
    position: absolute;
    border-radius: 22px;
    overflow: hidden;
    box-shadow: 0 18px 40px rgba(0,0,0,.45);
  }

  /* Front */
  .card-front {
    left: 150px; top: 140px;
    width: 360px; height: 630px;
    background: var(--paper);
  }
  .card-front .swoosh { position: absolute; inset: 0; width: 100%; height: 100%; }
  .front-brand {
    position: absolute; top: 70px; left: 0; right: 0;
    display: flex; flex-direction: column; align-items: center; gap: 16px;
  }
  .brand-dot { width: 64px; height: 64px; border-radius: 50%; background: var(--brand-green); }
  .brand-name {
    font-weight: 700; font-size: 22px; letter-spacing: .5px;
    color: var(--ink); text-transform: uppercase;
  }
  .contact {
    position: absolute; right: 26px; bottom: 40px;
    text-align: right; color: var(--white);
  }
  .contact-name { font-weight: 700; font-size: 24px; text-transform: uppercase; }
  .contact-role { font-size: 16px; text-transform: uppercase; margin-bottom: 16px; }
  .contact-address { font-size: 15px; line-height: 1.35; margin-bottom: 14px; }
  .contact-lines { list-style: none; font-size: 15px; line-height: 1.55; }
  .contact-lines li { display: flex; justify-content: flex-end; align-items: center; gap: 8px; }
  .contact-lines svg { width: 14px; height: 14px; fill: var(--white); }

  /* Back */
  .card-back {
    left: 560px; top: 380px;
    width: 560px; height: 320px;
    background: var(--brand-green);
  }
  .back-brand {
    position: absolute; left: 70px; top: 88px;
    display: flex; align-items: center; gap: 22px;
  }
  .back-brand .brand-dot { width: 86px; height: 86px; background: var(--ink); }
  .back-brand .brand-name { font-size: 30px; }
  .tagline {
    position: absolute; left: 70px; bottom: 60px;
    font-size: 17px; color: var(--ink);
  }
</style>
</head>
<body>

<section class="card card-front" aria-label="Card front">
  <svg class="swoosh" viewBox="0 0 360 630" preserveAspectRatio="none" aria-hidden="true">
    <path d="M0 430 C 120 350, 260 330, 330 200 C 345 170, 352 140, 360 120 L360 630 L0 630 Z" fill="#1e1e1e"/>
    <path d="M0 445 C 120 365, 262 348, 336 215 C 348 190, 355 165, 360 150 L360 630 L0 630 Z" fill="#ffffff"/>
    <path d="M0 452 C 120 372, 264 356, 338 222 C 350 198, 356 176, 360 162 L360 630 L0 630 Z" fill="var(--brand-green)"/>
  </svg>

  <div class="front-brand">
    <span class="brand-dot"></span>
    <span class="brand-name">The Stonebrace Co.</span>
  </div>

  <div class="contact">
    <p class="contact-name">Dale Morrow</p>
    <p class="contact-role">CEO/Founder</p>
    <p class="contact-address">2210- 48B Avenue<br>Nisku, Alberta T9E 1K2</p>
    <ul class="contact-lines">
      <li>780.555.0142
        <svg viewBox="0 0 24 24"><path d="M6.6 10.8a15 15 0 0 0 6.6 6.6l2.2-2.2a1 1 0 0 1 1-.25 11.4 11.4 0 0 0 3.6.57 1 1 0 0 1 1 1V20a1 1 0 0 1-1 1A17 17 0 0 1 3 4a1 1 0 0 1 1-1h3.5a1 1 0 0 1 1 1c0 1.25.2 2.45.57 3.6a1 1 0 0 1-.25 1z"/></svg></li>
      <li>780.555.0187
        <svg viewBox="0 0 24 24"><path d="M7 1h10a2 2 0 0 1 2 2v18a2 2 0 0 1-2 2H7a2 2 0 0 1-2-2V3a2 2 0 0 1 2-2zm0 3v14h10V4z"/></svg></li>
      <li>780.555.0119
        <svg viewBox="0 0 24 24"><path d="M5 3h14v7H5zM3 11h18v9H3zm4 2v2h10v-2z"/></svg></li>
      <li>dale@stonebrace.com
        <svg viewBox="0 0 24 24"><path d="M2 5h20v14H2zm2 2v.5l8 5 8-5V7l-8 5z"/></svg></li>
      <li>www.stonebrace.ca
        <svg viewBox="0 0 24 24"><path d="M12 2a10 10 0 1 0 0 20 10 10 0 0 0 0-20zm0 2c1.2 1.5 2 3.6 2.2 7H9.8C10 7.6 10.8 5.5 12 4zM4.1 13h3.7c.1 2.2.6 4.2 1.4 5.6A8 8 0 0 1 4.1 13zm0-2a8 8 0 0 1 5.1-5.6C8.4 6.8 7.9 8.8 7.8 11zm5.7 2h4.4c-.2 3.4-1 5.5-2.2 7-1.2-1.5-2-3.6-2.2-7zm6.4 0h3.7a8 8 0 0 1-5.1 5.6c.8-1.4 1.3-3.4 1.4-5.6zm0-2c-.1-2.2-.6-4.2-1.4-5.6A8 8 0 0 1 19.9 11z"/></svg></li>
    </ul>
  </div>
</section>

<section class="card card-back" aria-label="Card back">
  <div class="back-brand">
    <span class="brand-dot"></span>
    <span class="brand-name">The Stonebrace Co.</span>
  </div>
  <p class="tagline">Crushing Solutions</p>
</section>

</body>
</html>
```